stationary deign for trucking company

im a trucking company looking for a professional set of stationary designs i deliver goods from point a to b
Updates

When submitting stationary designs I need envelope design, letterhead, cards, I’d badge etc

Industry/Entity Type

Trucking Company

Requirements
Must have
• must have letter head, business card, envelope, fax sheet, id badge, folder, thank you card, notebook, invoice sheet.
Nice to have
• nice to have them all custom made (letterhead,envelope, business card, I’d badge etc
Should not have
• must not have prepaid sign want i unique design for items

```html
<!DOCTYPE html>
<html lang="en">
<head>
<meta charset="utf-8">
<title>Harlow Freight Lines – Business Card</title>
<link rel="stylesheet" href="https://fonts.googleapis.com/css2?family=Arimo:wght@400;700&display=swap">
<style>
  :root {
    --page: #ffffff;
    --card: #ffffff;
    --brand-blue: #1b5ca8;
    --logo-panel: #d4d4d4;
    --ink: #161616;
    --white: #ffffff;
  }
  html, body {
    margin: 0;
    padding: 0;
    width: 1200px;
    height: 1200px;
    overflow: hidden;
    background: var(--page);
    font-family: "Arimo", Arial, sans-serif;
  }
  .canvas {
    position: relative;
    width: 1200px;
    height: 1200px;
  }
  .card {
    position: absolute;
    left: 180px;
    width: 840px;
    height: 480px;
    background: var(--card);
    overflow: hidden;
    outline: 1px solid #ececec;
  }
  .card--front { top: 84px; }
  .card--back  { top: 636px; }

  .logo-panel {
    position: absolute;
    left: 193px;
    top: 0;
    width: 453px;
    height: 192px;
    background: var(--logo-panel);
    display: flex;
    align-items: center;
    justify-content: center;
    gap: 16px;
  }
  .logo-panel__square {
    width: 34px;
    height: 34px;
    background: var(--brand-blue);
  }
  .company-name {
    font-weight: 700;
    font-size: 34px;
    letter-spacing: 3px;
    color: var(--ink);
    line-height: 1;
  }

  .name-pointer {
    position: absolute;
    left: 0;
    top: 258px;
  }
  .person-name {
    position: absolute;
    left: 86px;
    top: 305px;
    margin: 0;
    font-size: 37px;
    font-weight: 700;
    color: var(--brand-blue);
    line-height: 1;
  }

  .contact-list {
    position: absolute;
    left: 408px;
    top: 250px;
    margin: 0;
    padding: 0;
    list-style: none;
    color: var(--ink);
    font-size: 21px;
    line-height: 26px;
  }
  .contact-item {
    position: relative;
    padding-left: 60px;
  }
  .contact-item--address { margin-bottom: 16px; }
  .contact-item + .contact-item:not(.contact-item--phone) { margin-top: 4px; }
  .contact-icon {
    position: absolute;
    left: 0;
    top: 1px;
    width: 24px;
    height: 24px;
  }

  .back-panel {
    position: absolute;
    left: 206px;
    top: 0;
    width: 455px;
    height: 480px;
    background: var(--brand-blue);
    display: flex;
    flex-direction: column;
    align-items: center;
    justify-content: center;
    gap: 26px;
  }
  .back-panel__square {
    width: 60px;
    height: 60px;
    background: var(--white);
  }
  .back-panel__name {
    color: var(--white);
    font-size: 46px;
    font-weight: 700;
    letter-spacing: 4px;
    text-align: center;
    line-height: 1.15;
  }
</style>
</head>
<body>
<main class="canvas">

  <section class="card card--front" aria-label="Business card front">
    <div class="logo-panel">
      <span class="logo-panel__square"></span>
      <span class="company-name">HARLOW FREIGHT</span>
    </div>

    <svg class="name-pointer" width="70" height="140" viewBox="0 0 70 140" aria-hidden="true">
      <polygon points="0,0 70,70 0,140" fill="var(--brand-blue)"/>
    </svg>
    <h1 class="person-name">YOUR NAME</h1>

    <ul class="contact-list">
      <li class="contact-item contact-item--address">
        <svg class="contact-icon" viewBox="0 0 24 24" aria-hidden="true">
          <rect width="24" height="24" rx="4" fill="var(--brand-blue)"/>
          <circle cx="12" cy="12" r="7" fill="var(--white)"/>
          <path d="M9 8 q3 2 1 5 q3 1 2 4" stroke="var(--brand-blue)" stroke-width="1.6" fill="none"/>
        </svg>
        YOUR ADDRESS HERE<br>12345
      </li>
      <li class="contact-item contact-item--phone">
        <svg class="contact-icon" viewBox="0 0 24 24" aria-hidden="true">
          <rect width="24" height="24" rx="4" fill="var(--brand-blue)"/>
          <path d="M12 20 C8 15 7 12.5 7 10.5 a5 5 0 0 1 10 0 c0 2-1 4.5-5 9.5z" fill="none" stroke="var(--white)" stroke-width="1.6"/>
          <circle cx="12" cy="10.5" r="1.8" fill="var(--white)"/>
        </svg>
        000111222
      </li>
      <li class="contact-item">
        <svg class="contact-icon" viewBox="0 0 24 24" aria-hidden="true">
          <rect width="24" height="24" rx="4" fill="var(--brand-blue)"/>
          <rect x="8" y="4" width="8" height="16" rx="1.5" fill="none" stroke="var(--white)" stroke-width="1.6"/>
          <circle cx="12" cy="17" r="1" fill="var(--white)"/>
        </svg>
        info@harlowfreight.com
      </li>
      <li class="contact-item">
        <svg class="contact-icon" viewBox="0 0 24 24" aria-hidden="true">
          <rect width="24" height="24" rx="4" fill="var(--brand-blue)"/>
          <rect x="5" y="7" width="14" height="10" rx="1" fill="var(--white)"/>
          <path d="M5.5 7.5 L12 12.5 L18.5 7.5" fill="none" stroke="var(--brand-blue)" stroke-width="1.5"/>
        </svg>
        harlowfreight.com
      </li>
    </ul>
  </section>

  <section class="card card--back" aria-label="Business card back">
    <div class="back-panel">
      <span class="back-panel__square"></span>
      <span class="back-panel__name">HARLOW<br>FREIGHT</span>
    </div>
  </section>

</main>
</body>
</html>
```